Construction Company

Design a clutter free business card, it can be double-sided utilizing the logo for VKM Ltd simple with all relevant contact information.

Please also a letterhead design to function for the purposes of invoicing, all mail requirements, with header to be distinctive while the footer ties page together and incorporates all necessary information.

For now, please use generic / dummy text and when a winner is selected, I will disclose the contact information.

Hi Designers! Please read the updated brief which includes the design of a business card and letterhead. Thank you!

```html
<!DOCTYPE html>
<html lang="en">
<head>
<meta charset="utf-8">
<title>VKM Ltd Letterhead</title>
<link href="https://fonts.googleapis.com/css2?family=Open+Sans:wght@400;600&display=swap" rel="stylesheet">
<style>
  :root {
    --navy: #233a87;
    --gold: #b08f2e;
    --ink: #8c8c8c;
    --contact: #4a4a4a;
    --paper: #ffffff;
    --backdrop: #e4e4e4;
  }
  * { margin: 0; padding: 0; box-sizing: border-box; }
  html, body {
    width: 1200px; height: 800px; overflow: hidden;
    background: var(--backdrop);
    font-family: "Open Sans", sans-serif;
  }
  .letterhead {
    position: absolute; left: 327px; top: 20px;
    width: 546px; height: 760px;
    background: var(--paper);
  }
  .brand {
    position: absolute; left: 49px; top: 72px;
    display: flex; align-items: center; gap: 8px;
    color: var(--navy); font-weight: 600; font-size: 36px; letter-spacing: 1px;
  }
  .brand-dot { width: 14px; height: 14px; border-radius: 50%; background: var(--navy); }
  .contact {
    position: absolute; right: 50px; top: 70px;
    list-style: none; font-size: 12px; line-height: 14.5px; color: var(--contact);
  }
  .contact li { display: flex; align-items: center; gap: 5px; }
  .contact svg { width: 10px; height: 10px; fill: var(--navy); }
  .letter-body {
    position: absolute; left: 49px; top: 196px; width: 447px;
    font-size: 10px; line-height: 14.6px; color: var(--ink);
  }
  .letter-body p { margin-bottom: 14.6px; text-align: justify; }
  .letter-body .salutation, .letter-body .closing { text-align: left; }
  .signature {
    position: absolute; left: 49px; top: 582px; width: 64px; height: 60px;
    background: linear-gradient(135deg, #e9e9e9, #d2d2d2);
  }
  .footer-band {
    position: absolute; left: 0; top: 718px; width: 100%; height: 24px;
    background: var(--navy);
    display: flex; align-items: center;
  }
  .footer-band .address {
    margin-left: 124px; display: flex; align-items: center; gap: 6px;
    color: #fff; font-size: 12.5px;
  }
  .footer-band .address svg { width: 10px; height: 13px; fill: #fff; }
  .footer-band .accent {
    position: absolute; right: 0; top: 0; width: 60px; height: 24px; background: var(--gold);
  }
</style>
</head>
<body>
  <main class="letterhead">
    <header>
      <div class="brand"><span class="brand-dot"></span>VKM Ltd</div>
      <ul class="contact">
        <li><svg viewBox="0 0 10 10"><path d="M1 3 C1 1 9 1 9 3 L9 4 L7 4 L7 3 L3 3 L3 4 L1 4 Z M2 5 L8 5 L9 9 L1 9 Z"/></svg>555.014.2290</li>
        <li><svg viewBox="0 0 10 10"><path d="M0 2 H10 V8 H0 Z M1 3 L5 6 L9 3" fill="none" stroke="#233a87" stroke-width="1"/></svg>office@vkmltd.com</li>
        <li><svg viewBox="0 0 10 10"><circle cx="5" cy="5" r="4.5"/><path d="M3 3 Q5 4 4 6 Q6 7 7 5" fill="none" stroke="#fff" stroke-width="1"/></svg>www.vkmltd.com</li>
      </ul>
    </header>

    <section class="letter-body">
      <p class="salutation">Dear customer,</p>
      <p>Lorem ipsum dolor sit amet, consectetur adipisicing elit, sed do eiusmod tempor incididunt ut labore et dolore magna aliqua. Ut enim ad minim veniam, quis nostrud exercitation ullamco laboris nisi ut aliquip ex ea commodo consequat. Duis aute irure dolor in reprehenderit in voluptate velit esse cillum dolore eu fugiat nulla pariatur. Excepteur sint occaecat cupidatat non proident, sunt in culpa qui officia deserunt mollit anim id est laborum.</p>
      <p>Lorem ipsum dolor sit amet, consectetur adipisicing elit, sed do eiusmod tempor incididunt ut labore et dolore magna aliqua. Ut enim ad minim veniam, quis nostrud exercitation ullamco laboris nisi ut aliquip ex ea commodo consequat. Duis aute irure dolor in reprehenderit in voluptate velit esse cillum dolore eu fugiat nulla pariatur. Excepteur sint occaecat cupidatat non proident, sunt in culpa qui officia deserunt mollit anim id est laborum.</p>
      <p>Lorem ipsum dolor sit amet, consectetur adipisicing elit, sed do eiusmod tempor incididunt ut labore et dolore magna aliqua. Ut enim ad minim veniam, quis nostrud exercitation ullamco laboris nisi ut aliquip ex ea commodo consequat. Duis aute irure dolor in reprehenderit in voluptate velit esse cillum dolore eu fugiat nulla pariatur. Excepteur sint occaecat cupidatat non proident, sunt in culpa qui officia deserunt mollit anim id est laborum.</p>
      <p class="closing">Lorem ipsum dolor sit amet, consectetur adipisicing elit, sed do eiusmod tempor incididunt ut labore et dolore magna aliqua. Ut enim ad minim veniam, quis nostrud exercitation ullamco laboris nisi ut aliquip ex ea commodo consequat. Duis aute irure dolor in reprehenderit.</p>
      <p class="closing">Yours Sincerely,</p>
    </section>

    <div class="signature" role="img" aria-label="Handwritten signature"></div>

    <footer class="footer-band">
      <div class="address">
        <svg viewBox="0 0 10 13"><path d="M5 0 C2 0 0 2 0 5 C0 8 5 13 5 13 C5 13 10 8 10 5 C10 2 8 0 5 0 Z M5 3 A2 2 0 1 0 5.01 3 Z" fill-rule="evenodd"/></svg>
        Harbour Court, 12 Mill Lane, London, E2 4RT
      </div>
      <div class="accent"></div>
    </footer>
  </main>
</body>
</html>
```